Events Company Needs Website Revamp

Tallwood Expos is an events company that specializes in organizing and marketing large scale consumer and trade events globally.

The new web design should provide easy classification of the events, and allow visitors to find and access the details page within 2 clicks.

There are no strict guidelines on the color theme. It just has to blend naturally with the corporate logo.
Updates

The company logo is uploaded (pdf & ai)

I came across this design which I like very much. Elegant and corporate with nice modern fonttype.

Layout wise, neat and clear. 

Please see how you can emulate the design further. Particularly, highlighting the 2 event arms (Trade/Consumer) clearly.

Target Market(s)

Consumer looking for upcoming events, B2C companies looking to participate, B2B companies looking to connect with other companies

Industry/Entity Type

It Company

Requirements
Must have
• The new design should help to achieve the following objectives:
1) Visitors should be able to easily identify and access the 2 different types of events (i.e. Trade Events and Consumer Events).
2) Visitors should be able to easily find events that interest them (e.g. filter by date, trade or consumer, category [i.e. beauty, retail, F&B, construction, etc.]).
3) Visitors should be able to access an event’s details page within 2 clicks from any page.

Main navigation to include the following links:
- About Us
- Calendar
- Consumer Events
- Trade Events
- Contact Us

Design for Three (3) pages required:
A. Homepage
- Clear differentiation and easy access to the 2 different types of events (trade and consumer)
- Featured area to showcase latest 4-5 events
- Quick way to access events calendar
- Clear call-to-action for newsletter signup
- Social media sharing widgets/buttons
- A section for latest news and press releases
- A section for featured testimonials

B. Events Listing Page
- List of links to all events
- Logos and/or photos of events
- Filter / tags to find events in a specific category (e.g. food, electronics, building & construction, etc.)

C. Events Details Page
- Photo strip to showcase event photos / brochure
- A section with event details (Date, Venue, Event Description, etc.)
- Call-to-action button to visit event website
- Call-to-action button to contact event sales team
- E.g. http://vantly-demo.com/user/brightfoxhk/brightfox-monday-2011 but with the photo strip permanently extended and of a shorter height. Event details and call-to-action buttons should also be easily seen

```html
<!DOCTYPE html>
<html lang="en">
<head>
<meta charset="utf-8">
<title>Tallwood Expos</title>
<link href="https://fonts.googleapis.com/css2?family=Arimo:ital,wght@0,400;0,700;1,400&display=swap" rel="stylesheet">
<style>
:root{
  --pink:#e0278a;
  --orange:#f7941d;
  --dark:#1f1f1f;
  --grey-text:#6b6b6b;
  --body-text:#555;
  --panel:#efefef;
  --panel-border:#d4d4d4;
  --purple:#5a2d91;
  --green:#5a9c1e;
  --title-orange:#f26b1d;
  --red:#c8102e;
  --blue-top:#3d93e2;
  --blue-bottom:#2769c0;
}
*{margin:0;padding:0;box-sizing:border-box}
html,body{width:821px;height:1200px;overflow:hidden}
body{position:relative;background:#fff;font-family:"Arimo",Arial,sans-serif;color:var(--body-text)}
.abs{position:absolute}
.top-area{left:0;top:0;width:821px;height:388px;background:linear-gradient(#fdfdfd,#e6e6e6 30%,#ececec 60%,#f3f3f3)}
.brand{left:50px;top:28px;display:flex;align-items:center;gap:8px}
.brand-mark{width:12px;height:12px;background:#444;display:block}
.brand-name{font-size:22px;color:#444;font-weight:400}
.parent-line{left:52px;top:78px;font-size:8px;color:#2a5aa8}
.search{left:592px;top:42px;width:122px;height:20px;background:#fff;border:1px solid #ddd;font-size:8px;color:#999;padding:5px}
.search svg{position:absolute;right:5px;top:3px}
.nav{left:35px;top:97px;width:745px;height:32px;background:var(--dark);display:flex;align-items:center;font-size:9px;font-weight:700}
.nav a{color:var(--pink);text-decoration:none;padding:0 6px}
.nav a.active{background:var(--pink);color:#5a0b35;height:32px;line-height:32px;width:55px;text-align:center;padding:0}
.banner{left:35px;top:140px;width:746px;height:200px;background:linear-gradient(#fba94a,var(--orange) 60%,#f58220)}
.banner-shadow{left:120px;top:338px;width:580px;height:24px;background:radial-gradient(ellipse at top,rgba(0,0,0,.25),transparent 70%)}
.banner h1{position:absolute;left:73px;top:8px;font-size:28px;font-weight:400;color:var(--pink);letter-spacing:-.3px}
.banner-photo{position:absolute;left:72px;top:50px;width:335px;height:97px;background:linear-gradient(90deg,#2d3e5c,#7c8aa3,#3a3a48);border:2px solid #fff}
.globe{position:absolute;left:478px;top:5px;width:180px;height:186px;border-radius:50%;background:radial-gradient(circle at 40% 35%,#fbd6a0,#e58b32 60%,#9c5418)}
.banner p{position:absolute;left:70px;top:154px;font-size:11.5px;color:#111;line-height:14px}
.arrow-btn{position:absolute;top:89px;width:24px;height:24px;border-radius:50%;background:rgba(255,255,255,.75);display:flex;align-items:center;justify-content:center}
.about{left:40px;top:400px;width:735px}
.about h2{font-size:13px;color:#222;width:355px;border-bottom:1px solid #ddd;padding-bottom:3px;margin-bottom:8px}
.about p{font-size:7.5px;line-height:9px;margin-bottom:8px;color:var(--grey-text)}
.band{height:22px;background:linear-gradient(#f7f7f7,#e6e6e6);border:1px solid #ccc;font-size:11px;font-weight:700}
.features{left:24px;top:530px;width:548px}
.band span{position:absolute;top:5px}
.feature{width:165px;top:560px;font-size:8px;line-height:12.5px;color:var(--grey-text)}
.feature .icon{width:28px;height:34px;margin:0 0 8px 8px;border-radius:4px}
.more{font-size:8px;font-weight:700;color:var(--green)}
.events{left:25px;top:691px;width:548px;color:var(--purple);font-size:10px}
.event-photo{height:34px;box-shadow:0 0 8px 3px rgba(60,140,255,.7)}
.logo-name{font-size:9px;font-weight:700;color:#333;display:flex;align-items:center;gap:3px}
.logo-name i{width:6px;height:6px;background:#333;display:block}
.event-title{font-size:10px;color:var(--title-orange)}
.event-info{font-size:8px;line-height:9.5px;color:#888;margin-top:8px}
.sidebar{left:596px;top:503px;width:214px;height:517px;background:var(--panel);border:1px solid var(--panel-border)}
.sidebar h3{font-size:12.5px;color:#222;font-weight:700}
.quote{font-size:8px;font-style:italic;color:#999;line-height:11.5px}
.news-item{font-size:7.5px;line-height:11.5px;color:var(--grey-text);border-bottom:1px solid #ddd;padding-bottom:8px;margin-bottom:6px}
.news-item b{color:#555}
.news-item em{font-weight:700;color:#444}
.news-item span{color:#2e9bd6;font-weight:700}
.cal-label{font-size:10px;color:var(--title-orange)}
.calendar{left:615px;top:783px;width:137px;background:#444;padding:2px}
.cal-head{height:22px;background:linear-gradient(#555,#2a2a2a);color:#fff;font-size:11px;display:flex;justify-content:space-between;align-items:center;padding:0 6px}
.calendar table{width:100%;border-collapse:separate;border-spacing:1px;background:#fff;font-size:9.5px;text-align:center}
.calendar th{font-size:6px;color:#333;font-weight:400;height:10px}
.calendar td{background:#e4e4e4;height:18px;color:#222;border:1px solid #ccc}
.calendar td.muted{color:#999;background:#eee}
.calendar td.today{background:#b22222;color:#222}
.calendar td.mark{background:#5a8f2a}
.calendar td.pick{background:var(--orange)}
.signup{left:633px;top:943px;font-size:9.5px;color:#8b1a1a;line-height:11px}
.signup-input{left:636px;top:972px;width:84px;height:18px;background:#fff;border:1px solid #ccc}
.join{left:662px;top:997px;width:56px;height:16px;border-radius:3px;background:linear-gradient(#e8444f,var(--red));color:#fff;font-size:9px;font-weight:700;text-align:center;line-height:16px}
.organised-label{left:72px;top:1015px;font-size:9px;color:#333}
.organised{left:57px;top:1027px;width:700px;height:97px;border:1px solid #ccc;border-radius:6px;background:linear-gradient(#fafafa,#eee)}
.organised .row{position:absolute;left:24px;top:25px;width:650px;display:flex;justify-content:space-between;align-items:center;height:40px}
.footer{left:0;top:1140px;width:821px;height:60px;background:linear-gradient(var(--blue-top),var(--blue-bottom))}
.footer-name{position:absolute;left:36px;top:22px;font-size:10px;color:#fff}
.footer small{position:absolute;font-size:7px;color:#fff}
.social{position:absolute;top:20px;width:16px;height:16px;border-radius:3px;background:#e8eef7}
</style>
</head>
<body>
<div class="abs top-area"></div>

<header>
  <div class="abs brand"><span class="brand-mark"></span><span class="brand-name">Tallwood Expos</span></div>
  <div class="abs parent-line">A SUBSIDIARY OF HMG</div>
  <div class="abs search">Search:
    <svg width="14" height="14" viewBox="0 0 14 14"><circle cx="6" cy="6" r="4" fill="none" stroke="#777" stroke-width="1.6"/><line x1="9" y1="9" x2="13" y2="13" stroke="#777" stroke-width="2"/></svg>
  </div>
  <nav class="abs nav">
    <a class="active" href="#">Home</a><a href="#">About Us</a><a href="#">Calendar</a><a href="#">Consumer Events</a><a href="#">Trade Events</a><a href="#">Contact us</a>
  </nav>
</header>

<section class="abs banner">
  <h1>Welcome to Tallwood Expos</h1>
  <div class="banner-photo" role="img" aria-label="Photo of guests and visitors at an exhibition opening"></div>
  <div class="globe" role="img" aria-label="Globe made of event photographs"></div>
  <p>Bringing about a whole new dimension of audience experience and engagement<br>by organizing events with focus on differentiated themes and event concepts.</p>
  <span class="arrow-btn" style="left:18px"><svg width="10" height="10" viewBox="0 0 10 10"><path d="M7 1 3 5l4 4" fill="none" stroke="#777" stroke-width="2"/></svg></span>
  <span class="arrow-btn" style="left:693px"><svg width="10" height="10" viewBox="0 0 10 10"><path d="M3 1l4 4-4 4" fill="none" stroke="#777" stroke-width="2"/></svg></span>
</section>
<div class="abs banner-shadow"></div>

<section class="abs about">
  <h2>About Tallwood</h2>
  <p>Being at the right place at the right time can spell success for your business. And Tallwood Expos links you to a dimension of immense possibilities, where people and ideas converge to create great shows and events to bring out the best in your business.</p>
  <p>Incorporated in April 2008 and wholly owned by Harbourline Media Group (HMG), Tallwood Expos, which stands for "Tallwood Events, Expos and Showcases", aims to the the leading lifestyle event company behind exciting and innovative fairs, shows, events and exhibitions for mid to high-end consumers.</p>
  <p>Backed by a committed and experienced team of professionals and HMG's comprehensive range of advertising platforms, these events with unique concepts will not only draw local audiences but also regional participants. Tallwood Expos is committed to building memorable and quality events which will be founded on research, planning, and established network of resources, and a wild but solid imagination. This commitment will in return result in a greater mileage for<br>our exhibitors.</p>
</section>

<div class="abs band features"><span style="left:19px">Innovate</span><span style="left:207px">Entertain</span><span style="left:385px">Value Added</span></div>
<div class="abs feature" style="left:44px"><div class="icon" role="img" aria-label="Light bulb icon" style="background:linear-gradient(#ffd27a,#f08a1c)"></div>Conceptualize events that are strongly themed and create synergy with business partners offerings.</div>
<div class="abs feature" style="left:230px"><div class="icon" role="img" aria-label="Film clapboard icon" style="background:linear-gradient(#8fd16a,#2f6fb8)"></div>Engage the audience in a whole new level of event experience with a plethora of engaging activities.</div>
<div class="abs feature" style="left:410px"><div class="icon" role="img" aria-label="Podcast icon" style="background:linear-gradient(#c9a4e8,#6a2f9c);border-radius:50%"></div>Bring extra value to our business partners with customized promotional opportunities and to our audience with best and exclusive offers at our shows.</div>
<a class="abs more" style="left:145px;top:663px">know more...</a>
<a class="abs more" style="left:330px;top:663px">know more...</a>
<a class="abs more" style="left:520px;top:663px">know more...</a>

<div class="abs band events"><span style="left:29px">Consumer Events</span><span style="left:309px">Trade Events &amp; Exhibitions</span></div>
<div class="abs event-photo" role="img" aria-label="Photo collage of consumer event crowds" style="left:48px;top:731px;width:180px;background:linear-gradient(90deg,#e48a2c,#b7c4d6,#d75a3a)"></div>
<div class="abs event-photo" role="img" aria-label="Photo of chefs and guests at a trade exhibition" style="left:315px;top:731px;width:212px;background:linear-gradient(90deg,#3b3b3b,#c9b8a0,#5b4636)"></div>

<div class="abs logo-name" style="left:45px;top:818px"><i></i>Orient Prestige</div>
<div class="abs" style="left:125px;top:811px"><div class="event-title">Orient Prestige</div><div class="event-info">Venue: Varies with individual programmes<br>Date: 01 - 31 January 2011<br>Time: Varies with individual programmes<br>Varies with individual programmes</div></div>

<div class="abs logo-name" style="left:38px;top:922px"><i></i>Paper Trail</div>
<div class="abs" style="left:126px;top:906px"><div class="event-title">Citywide Paper Trail 2011</div><div class="event-info">Venue: TBC<br>Date: 27 - 27 August 2011 , Saturday - Saturday<br>Time: 7:30am - 12:30pm<br>TBC</div></div>

<div class="abs logo-name" style="left:314px;top:816px"><i></i>LaunchPad Asia</div>
<div class="abs" style="left:416px;top:814px"><div class="event-title">LaunchPad Asia</div><div class="event-info" style="margin-top:3px">Venue: Helix Hall, Singapore<br>18 Quarry Lane, Singapore S120455<br>Date: 29 February 2012 - 02 December 2011 ,<br>Wednesday - Friday<br>Time: 09:00 - 20:00</div></div>

<div class="abs logo-name" style="left:313px;top:898px"><i></i>StructaExpo 2012</div>
<div class="abs" style="left:420px;top:898px"><div class="event-title">StructaExpo 2012</div><div class="event-info" style="margin-top:3px">Venue: Harbourfront Convention Hall<br>Date: 15 - 17 May 2012 , Tuesday - Thursday<br>Time: 10am - 6pm<br>Admission is restricted to trade professionals<br>only and there is no charge to visit the<br>exhibition</div></div>

<aside class="abs sidebar">
  <h3 style="position:absolute;left:16px;top:11px">Testimonials</h3>
  <p class="quote" style="position:absolute;left:20px;top:30px">"Quis autem vel eum iure reprehenderit<br>qui in ea voluptate velit esse voluptas<br>nulla pariatur?"</p>
  <p style="position:absolute;left:82px;top:70px;font-size:7.5px;color:#333"><i><b>-Dana Whitlock,</b></i> <span style="color:#777">Ferncrest Co</span></p>
  <h3 style="position:absolute;left:13px;top:94px">News &amp; Press Releases</h3>
  <div style="position:absolute;left:13px;top:124px;width:192px">
    <div class="news-item"><b>Lorem Ipsum as their default model text...</b><br>There are many variations of passages of Lorem Ipsum available, but the majority have suffered.<br><em>19-11-09</em> <span>- 2 comments</span></div>
    <div class="news-item"><b>Lorem Ipsum as their default model text...</b><br>All the Lorem Ipsum generators on the Internet tend to repeat predefined chunks as necessary.<br><em>19-11-09</em> <span>- 3 comments</span></div>
  </div>
  <div class="cal-label" style="position:absolute;left:18px;top:258px">EVENTS CALENDAR</div>
</aside>

<div class="abs calendar">
  <div class="cal-head"><span>&#9664;</span><span>January 2012</span><span>&#9654;</span></div>
  <table>
    <tr><th>SUN</th><th>MON</th><th>TUE</th><th>WED</th><th>THU</th><th>FRI</th><th>SAT</th></tr>
    <tr><td class="today">1</td><td>2</td><td>3</td><td>4</td><td>5</td><td class="mark">6</td><td>7</td></tr>
    <tr><td>8</td><td>9</td><td>10</td><td>11</td><td>12</td><td>13</td><td>14</td></tr>
    <tr><td>15</td><td>16</td><td>17</td><td>18</td><td>19</td><td>20</td><td class="pick">21</td></tr>
    <tr><td>22</td><td>23</td><td>24</td><td>25</td><td>26</td><td>27</td><td>28</td></tr>
    <tr><td>29</td><td>30</td><td>31</td><td class="muted">1</td><td class="muted">2</td><td class="muted">3</td><td class="muted">4</td></tr>
    <tr><td class="muted">5</td><td class="muted">6</td><td class="muted">7</td><td class="muted">8</td><td class="muted">9</td><td class="muted">10</td><td class="muted">11</td></tr>
  </table>
</div>
<p class="abs signup">Join our newsletter list<br>to get the latest updates</p>
<div class="abs signup-input"></div>
<div class="abs join">Join Now</div>

<div class="abs organised-label">EVENTS ORGANISED:</div>
<section class="abs organised">
  <svg style="position:absolute;left:4px;top:36px" width="10" height="20" viewBox="0 0 10 20"><path d="M8 2 2 10l6 8" fill="none" stroke="#444" stroke-width="2"/></svg>
  <div class="row">
    <span class="logo-name"><i></i>WorkspaceFair 2012</span>
    <span class="logo-name">Food Fest</span>
    <span class="logo-name"><i></i>StructaExpo 2012</span>
    <span class="logo-name">Little Ones 2012</span>
    <span class="logo-name">Young Minds 2012</span>
    <span class="logo-name">LaunchPad Asia 2012</span>
  </div>
  <svg style="position:absolute;right:4px;top:36px" width="10" height="20" viewBox="0 0 10 20"><path d="M2 2l6 8-6 8" fill="none" stroke="#444" stroke-width="2"/></svg>
</section>

<footer class="abs footer">
  <span class="footer-name">Tallwood Expos</span>
  <small style="left:113px;top:23px">Copyright © Tallwood Expos 2008-2010. All Rights Reserved.</small>
  <small style="left:332px;top:24px">Tel: (65) 6100-2040 or (65) 6100-2041 • Fax: (65) 6100-2090 • hello@tallwoodexpos.com</small>
  <span class="social" style="left:640px"></span>
  <span class="social" style="left:660px"></span>
  <span class="social" style="left:680px"></span>
  <span class="social" style="left:700px"></span>
  <span class="social" style="left:720px"></span>
</footer>
</body>
</html>
```